Business card for a Exhibition booth fabrication company

Hi. My company would like to change our corporate name card. We are an events and Exhibition stand builder company. We would like our corporate name card to resonate what we do. I need someone to create something unique that relates to the industry that I am in. The graphic designer should be creative to incorporate the elements of my industry and try to blend in well in the design of the card. Our aim is to ensure that we are unique and our card can look different from our competitors.
Updates

Target Market(s)

Marketing and events manager from all companies

Contact Information for Business Card

The business card should have the following details:
Name
Job Title
Email
Website

Colors

Designer to choose colors to be used in the design.

Requirements
Must have
• The card must be look something that is relevant to the service that I am providing. My website is: www.velmora-buildworks.com
• You can see my website to get more information on what service that I am doing
Nice to have
• On the back of my card, I would like to have a globe image with the incorporation of my company logo. This is to indicate that my services can be done in any part of the world.

```html
<!DOCTYPE html>
<html lang="en">
<head>
<meta charset="UTF-8">
<title>Velmora Buildworks – Business Card</title>
<link href="https://fonts.googleapis.com/css2?family=Open+Sans:wght@400;600;700&display=swap" rel="stylesheet">
<style>
  :root {
    --page-bg: #2b2b2d;
    --card-bg: #4a4a4d;
    --card-bg-back: #505053;
    --map-tone: #5c5c60;
    --text-light: #ffffff;
    --text-soft: #e6e6e6;
    --accent-red: #e0242b;
    --divider: #8a8a8e;
  }
  * { margin: 0; padding: 0; box-sizing: border-box; }
  html, body {
    width: 1200px; height: 900px; overflow: hidden;
    background: var(--page-bg);
    font-family: "Open Sans", Arial, sans-serif;
  }
  .canvas { position: relative; width: 1200px; height: 900px; }

  .card {
    position: absolute;
    width: 620px; height: 354px;
    border-radius: 22px;
    overflow: hidden;
  }

  /* Front */
  .card-front { left: 110px; top: 70px; background: var(--card-bg); }
  .front-brand {
    position: absolute; left: 40px; top: 150px; width: 230px;
    color: var(--text-light);
    font-size: 26px; font-weight: 700; line-height: 1.2;
    letter-spacing: 1px; text-align: center;
  }
  .front-divider {
    position: absolute; left: 300px; top: 70px;
    width: 1px; height: 214px; background: var(--divider);
  }
  .contact { position: absolute; left: 330px; top: 82px; color: var(--text-soft); }
  .contact-name { font-size: 17px; font-weight: 700; color: var(--text-light); letter-spacing: 0.5px; }
  .contact-title { font-size: 14px; color: var(--accent-red); margin-bottom: 10px; }
  .contact-address { font-size: 14px; line-height: 1.45; margin-bottom: 14px; }
  .contact-line { display: flex; align-items: center; gap: 8px; font-size: 14px; margin-bottom: 6px; }
  .contact-line svg { width: 16px; height: 16px; flex: none; }

  /* Back */
  .card-back { left: 470px; top: 476px; background: var(--card-bg-back); }
  .world-map {
    position: absolute; left: 30px; top: 20px; width: 560px; height: 260px;
    border-radius: 40% 45% 38% 42%;
    background: radial-gradient(ellipse at center, var(--map-tone) 0%, rgba(92,92,96,0.5) 60%, rgba(92,92,96,0) 100%);
  }
  .back-brand {
    position: absolute; left: 0; right: 0; top: 128px;
    text-align: center; color: var(--accent-red);
    font-size: 30px; font-weight: 700; letter-spacing: 2px;
  }
  .back-web {
    position: absolute; left: 0; right: 0; top: 288px;
    display: flex; align-items: center; justify-content: center; gap: 14px;
    color: var(--text-light); font-size: 15px;
  }
  .back-web .rule { width: 60px; height: 1px; background: var(--text-soft); }
  .back-web .highlight { color: var(--accent-red); }
</style>
</head>
<body>
<main class="canvas">
  <section class="card card-front">
    <div class="front-brand">VELMORA<br>BUILDWORKS</div>
    <div class="front-divider"></div>
    <div class="contact">
      <p class="contact-name">DANIEL REYES</p>
      <p class="contact-title">President</p>
      <p class="contact-address">P.O. Box 4120,<br>Harbor Lane, Westfield</p>
      <p class="contact-line">
        <svg viewBox="0 0 16 16" aria-hidden="true"><circle cx="8" cy="8" r="7" fill="none" stroke="#fff" stroke-width="1.2"/><path d="M5.5 4.5l1.5 0 .6 2-1 .8a5 5 0 0 0 2.1 2.1l.8-1 2 .6 0 1.5a1 1 0 0 1-1 1A6 6 0 0 1 4.5 5.5a1 1 0 0 1 1-1z" fill="#fff"/></svg>
        +00 5550 1842
      </p>
      <p class="contact-line">
        <svg viewBox="0 0 16 16" aria-hidden="true"><circle cx="8" cy="8" r="7" fill="none" stroke="#fff" stroke-width="1.2"/><rect x="4" y="5.5" width="8" height="5.5" fill="none" stroke="#fff" stroke-width="1"/><path d="M4 5.5l4 3 4-3" fill="none" stroke="#fff" stroke-width="1"/></svg>
        info@velmora-buildworks.com
      </p>
    </div>
  </section>

  <section class="card card-back">
    <div class="world-map" role="img" aria-label="Faint world map spanning the card background"></div>
    <div class="back-brand">VELMORA BUILDWORKS</div>
    <div class="back-web">
      <span class="rule"></span>
      <span>www.<span class="highlight">velmora-buildworks</span>.com</span>
      <span class="rule"></span>
    </div>
  </section>
</main>
</body>
</html>
```